Business Card Design

We like to use greens as you will see in our logo (but not TOO much green). We are a Dental Clinic in a somewhat eccentric community. We do not like the dated sharp designs which we see many dentists use. We're looking for something bright and fresh while still maintaining the integrity of the profession. Elegance is not necessarily what we are going for... we need for the design to be "mature" but also up-lifting.

See our logo.
Updates

Project Deadline Extended
Reason: We have 5 designs which we like. But we'd like to see a few more before committing to a design.

Project Deadline Extended
Reason: We are awaiting revisions to this project. We are still welcoming designs while we wait to see if designers are able to provide to us the revisions we require in order to proceed with a selection.

Target Market(s)

Younger families - ages late 20's to early 40's

Industry/Entity Type

Business

Contact Information for Business Card

Corwel T. Banfry DDS 2730 W. Halvert Rd. Ste. 7 Fernhollow, OR 48391 (555)555-0174 FX (555)555-0189 info@BrightwellDentalCareMi.com BrigthwellDentalCareMi.com on the back of the card we need an appointment reminder (For____ Date___ Time____) with "If you are unable to keep your appointment, kindly give 48 hours notice" at the bottom. No use of teeth in the design. DOUBLE SIDED DESIGN

Requirements
Should not have
• The use of pictures of teeth

```html
<!DOCTYPE html>
<html lang="en">
<head>
<meta charset="utf-8">
<title>Brightwell Dental Care – Business Card</title>
<link rel="stylesheet" href="https://fonts.googleapis.com/css2?family=Source+Sans+3:ital,wght@0,400;0,600;0,700;1,400&family=Marcellus&display=swap">
<style>
  :root {
    --green-dark: #1f6b34;
    --green-light: #8cc63f;
    --ink: #3a3a3a;
    --paper: #ffffff;
    --backdrop: #ecebe6;
    --rule: #8a8a8a;
    --frame: #555555;
  }
  * { margin: 0; padding: 0; box-sizing: border-box; }
  html, body { width: 1200px; height: 1179px; overflow: hidden; }
  body {
    background: var(--backdrop);
    position: relative;
    font-family: "Source Sans 3", Arial, sans-serif;
    color: var(--ink);
  }
  .card {
    position: absolute;
    background: var(--paper);
    border-radius: 30px;
    overflow: hidden;
    box-shadow: 0 2px 6px rgba(0,0,0,.18);
  }
  .card-front { left: 26px; top: 46px; width: 918px; height: 524px; }
  .card-back  { left: 249px; top: 622px; width: 917px; height: 523px; border: 2px solid var(--frame); }

  .brand { position: absolute; display: flex; align-items: center; color: var(--green-dark); font-weight: 600; }
  .brand-dot { border-radius: 50%; background: var(--green-light); flex: none; }
  .brand-name { line-height: 0.95; }
  .brand-name span { display: block; }

  .card-front .brand { left: 62px; top: 170px; gap: 18px; }
  .card-front .brand-dot { width: 58px; height: 58px; }
  .card-front .brand-name .line-1 { font-size: 60px; }
  .card-front .brand-name .line-2 { font-size: 36px; letter-spacing: 1px; }

  .divider { position: absolute; left: 487px; top: 92px; width: 2px; height: 236px; background: var(--rule); }

  .contact-list { position: absolute; left: 511px; top: 88px; list-style: none; font-size: 23px; }
  .contact-list li { display: flex; align-items: center; gap: 8px; height: 39.5px; }
  .contact-list svg { width: 20px; height: 20px; fill: var(--green-dark); flex: none; }
  .address { position: absolute; left: 511px; top: 262px; font-size: 23px; line-height: 31px; }

  .wave { position: absolute; left: 0; top: 0; width: 918px; height: 524px; }
  .doctor { position: absolute; right: 28px; top: 448px; text-align: right; color: var(--paper); }
  .doctor-name { font-size: 29px; font-weight: 700; line-height: 34px; }
  .doctor-title { font-size: 22px; line-height: 30px; }

  .card-back .brand { left: 72px; top: 40px; gap: 14px; }
  .card-back .brand-dot { width: 40px; height: 40px; }
  .card-back .brand-name .line-1 { font-size: 48px; }
  .card-back .brand-name .line-2 { font-size: 29px; letter-spacing: 1px; }

  .appointment-title { position: absolute; left: 76px; top: 160px; font-family: "Marcellus", Georgia, serif; font-weight: 400; font-size: 36px; color: var(--green-dark); letter-spacing: 1px; }
  .field { position: absolute; font-size: 24px; display: flex; align-items: baseline; }
  .dots { display: inline-block; border-bottom: 2px dotted #666; height: 1px; margin: 0 4px; }
  .field-name { left: 80px; top: 238px; }
  .field-name .dots { width: 500px; margin-left: 10px; }
  .field-date { left: 80px; top: 303px; }
  .field-date .dots.date { width: 160px; margin-left: 28px; margin-right: 10px; }
  .field-date .dots.time { width: 156px; margin-left: 10px; }
  .field-next { left: 80px; top: 377px; align-items: center; }
  .slot { width: 165px; height: 36px; border: 2px solid var(--frame); border-radius: 5px; margin-left: 16px; }
  .slot + .slot { margin-left: 38px; }

  .days { position: absolute; right: 180px; top: 78px; list-style: none; }
  .days li { position: absolute; right: 0; display: flex; align-items: center; gap: 18px; font-size: 25px; font-weight: 600; }
  .days .box { width: 55px; height: 34px; border: 2px solid var(--frame); border-radius: 4px; margin-right: -76px; }

  .notice { position: absolute; left: 0; right: 0; top: 448px; text-align: center; font-style: italic; font-size: 25px; }
</style>
</head>
<body>

<section class="card card-front">
  <svg class="wave" viewBox="0 0 918 524" aria-hidden="true">
    <path d="M0,318 C110,420 250,472 400,468 C600,458 760,345 918,350 L918,524 L0,524 Z" fill="var(--green-light)"/>
    <path d="M0,350 C120,440 260,488 400,484 C600,474 760,372 918,376 L918,524 L0,524 Z" fill="var(--paper)"/>
    <path d="M0,366 C120,455 260,500 400,496 C600,486 760,388 918,392 L918,524 L0,524 Z" fill="var(--green-dark)"/>
  </svg>

  <div class="brand">
    <span class="brand-dot"></span>
    <div class="brand-name"><span class="line-1">Brightwell</span><span class="line-2">DENTAL CARE</span></div>
  </div>

  <div class="divider"></div>

  <ul class="contact-list">
    <li><svg viewBox="0 0 20 20"><path d="M5 2l3 4-2 2c1 2 3 4 5 5l2-2 4 3-2 3C9 17 3 11 2 5z"/></svg>(555)555-0174</li>
    <li><svg viewBox="0 0 20 20"><path d="M5 2h10v5H5zM2 8h16v8h-3v2H5v-2H2zM7 13v3h6v-3z"/></svg>(555)555-0189</li>
    <li><svg viewBox="0 0 20 20"><path d="M2 5h16v11H2zM3 6l7 5 7-5v-0.5H3z" fill-rule="evenodd"/></svg>info@BrightwellDentalCareMi.com</li>
    <li><svg viewBox="0 0 20 20"><path d="M10 2a8 8 0 100 16 8 8 0 000-16zm0 2c1 1.5 1.5 3.5 1.6 5H8.4C8.5 7.5 9 5.5 10 4zm-6 5c.3-2 1.5-3.7 3.3-4.5C6.7 6 6.4 7.5 6.4 9zm0 2h2.4c0 1.5.3 3 .9 4.5C5.5 14.7 4.3 13 4 11zm4.4 0h3.2c-.1 1.5-.6 3.5-1.6 5-1-1.5-1.5-3.5-1.6-5zm5.2 0H16c-.3 2-1.5 3.7-3.3 4.5.6-1.5.9-3 .9-4.5zm0-2c0-1.5-.3-3-.9-4.5C14.5 5.3 15.7 7 16 9z"/></svg>BrigthwellDentalCareMi.com</li>
  </ul>

  <p class="address">2730 W. Halvert Rd.<br>Ste. 7 Fernhollow, OR 48391</p>

  <div class="doctor">
    <p class="doctor-name">Corwel T. Banfry</p>
    <p class="doctor-title">DDS</p>
  </div>
</section>

<section class="card card-back">
  <div class="brand">
    <span class="brand-dot"></span>
    <div class="brand-name"><span class="line-1">Brightwell</span><span class="line-2">DENTAL CARE</span></div>
  </div>

  <h2 class="appointment-title">YOUR APPOINTMENT</h2>

  <p class="field field-name">Name :<span class="dots"></span></p>
  <p class="field field-date">Date :<span class="dots date"></span>Time :<span class="dots time"></span>am / pm</p>
  <div class="field field-next">Next Appointment<span class="slot"></span><span class="slot"></span></div>

  <ul class="days">
    <li style="top:0">MON<span class="box"></span></li>
    <li style="top:64px">TUE<span class="box"></span></li>
    <li style="top:126px">WED<span class="box"></span></li>
    <li style="top:191px">THU<span class="box"></span></li>
    <li style="top:248px">FRI<span class="box"></span></li>
    <li style="top:304px">SAT<span class="box"></span></li>
  </ul>

  <p class="notice">f you are unable to keep your appointment, kindly give 48 hours notice</p>
</section>

</body>
</html>
```